Sparkling Wine Label Mirren Hollow

Super Premium Sparkling Wine Label

We are a super premium tasmanian fine wine producer and are about to release our first Sparking Wine.

please visit www.mirrenhollow-example.com.au to check out our range of wine. We need a label that will sit within this branding but as the aspirational product. We think that the Vosse grey/navy label will fit into this concept. It is masculine clean elegent and very smick,
and would be a great addition to our line see Argent Pinot Noir label.

However you can be quite creative with Sparkling Line eg Belvane Royal Cuvee is a stunning classical french label featuring gold baroque detail and feminine elegence.

Its up to you if you where spending $50 on a special bottles of sparkling wine what would you expect to see?

Black/Gold Graphite/Gold

Needs a neck /collar label

Main Front Label
Mirren Hollow
Chardonnay Pinot Noir
Tasmania

Back label has all the techical into you can use the back label from existing labels but reverserve out the colours to black and white or graphite and white

We want a label that oozes quality and expense. That says this the way I want to celebrate.

Target Market(s)

40 60 age group appreciator of quality

Industry/Entity Type

Product

Requirements
Must have
• Neck label
Simular to Vosse Shield so
MIRREN arched above
G rondel in middle possibiliy replacing coat of arms
TASMANIA arched under in red

Main Front Label
Mirren Hollow
Tasmania
Chardonnay Pinot Noir 750ML

Back Label / use the attachment Mirren label just reverse out so that it is a black label with white writing and amend information
Mirren Hollow
23 Pell Morrow Rd Ashvale
Tasmania, 7261
0412557390
www.mirrenhollow-example.com.au
contact@mirrenhollow-example.com.au
Sulphur Dioxide Added
Alc/Vol 12.5%
7.7 Standard Drinks

Rondel g

```html
<!DOCTYPE html>
<html lang="en">
<head>
<meta charset="utf-8">
<title>Mirren Hollow – Back Label</title>
<link rel="stylesheet" href="https://fonts.googleapis.com/css2?family=Tinos&display=swap">
<style>
  :root {
    --page: #ffffff;
    --rim: #c7a47a;
    --edge-dark: #17110c;
    --mid-dark: #4a3724;
    --bronze: #b5936a;
    --ink: #f4eee5;
    --name-gold: #e0cba4;
    --ornament: rgba(196, 160, 118, 0.28);
  }
  html, body {
    margin: 0;
    padding: 0;
    width: 1200px;
    height: 923px;
    overflow: hidden;
    background: var(--page);
  }
  .canvas {
    position: relative;
    width: 1200px;
    height: 923px;
  }
  .back-label {
    position: absolute;
    left: 206px;
    top: 97px;
    width: 676px;
    height: 774px;
    box-sizing: border-box;
    border: 6px solid var(--rim);
    border-radius: 78px;
    overflow: hidden;
    background: linear-gradient(90deg,
      var(--edge-dark) 0%,
      var(--mid-dark) 22%,
      var(--bronze) 49%,
      var(--mid-dark) 78%,
      var(--edge-dark) 100%);
    font-family: "Tinos", "Times New Roman", serif;
    color: var(--ink);
    text-align: center;
  }
  .ornament {
    position: absolute;
    width: 150px;
    height: 150px;
    background: radial-gradient(circle at center, var(--ornament) 0%, rgba(196,160,118,0.12) 45%, rgba(196,160,118,0) 72%);
  }
  .ornament--top-left { left: 40px; top: 22px; }
  .ornament--top-right { right: 24px; top: 22px; }
  .ornament--bottom-left { left: 24px; bottom: 20px; }
  .ornament--bottom-right { right: 14px; bottom: 20px; }

  .brand-name {
    position: absolute;
    left: 0;
    right: 0;
    top: 175px;
    margin: 0;
    font-size: 58px;
    font-weight: 400;
    color: var(--name-gold);
    letter-spacing: 1px;
  }
  .details {
    position: absolute;
    left: 0;
    right: 0;
    margin: 0;
    font-size: 29px;
    line-height: 35px;
  }
  .address { top: 338px; }
  .web { top: 481px; }
  .additive { top: 584px; }
  .volume {
    position: absolute;
    top: 655px;
    left: 0;
    right: 0;
    font-size: 29px;
    line-height: 35px;
  }
  .volume .abv { position: absolute; left: 161px; }
  .volume .size { position: absolute; left: 416px; }
  .standard-drinks { top: 708px; }
</style>
</head>
<body>
<div class="canvas">
  <section class="back-label">
    <div class="ornament ornament--top-left" role="img" aria-label="Gold baroque filigree corner ornament"></div>
    <div class="ornament ornament--top-right" role="img" aria-label="Gold baroque filigree corner ornament"></div>
    <div class="ornament ornament--bottom-left" role="img" aria-label="Gold baroque filigree corner ornament"></div>
    <div class="ornament ornament--bottom-right" role="img" aria-label="Gold baroque filigree corner ornament"></div>

    <h1 class="brand-name">Mirren Hollow</h1>

    <p class="details address">23 Pell Morrow Rd Ashvale<br>Tasmania, 7261<br>0412557390</p>
    <p class="details web">www.mirrenhollow-example.com.au<br>contact@mirrenhollow-example.com.au</p>
    <p class="details additive">Sulphur Dioxide Added</p>
    <div class="volume"><span class="abv">Alc/Vol 12.5%</span><span class="size">750 Ml</span></div>
    <p class="details standard-drinks">7.7 Standard Drinks</p>
  </section>
</div>
</body>
</html>
```